Wesbite design for Investment Firm

We want a basic (clean) website that follows the form, fonts and colors of our attachments. This is for a financial investment management firm, but we have a boutique (anti-Wall Street) approach. Site should have an Home Page (Logo up top - room for basic copy on bottom, Philosophy Page (room for Quarterly Letter attachment and basic copy, Performance Page (room for Performance Overview and Performance Analysis and basic copy), Team Page, Commentary Page and Contact

Reason: Some designers have asked for an extension. Again, please only use image of Train Station or Train Station Logo in design.

Target Market(s)

Small and mid-size financial advisors from across the country

Industry/Entity Type

Financial

Number of Pages Required

5+ page

Font styles to use
Other font styles liked:
• Palotino Linotype

Colors
3176b5
cfdeed
ffffff

Requirements
Must have
• Please refer to existing site www.qlvor.example. Of note, this is too complex / cluttered. We simply want Blur, Grey and White consistent with attachments. The copy is pretty good, but will be simplified (and no quotes)
Should not have
• No images other than train station logo and / or train station image

```html
<!DOCTYPE html>
<html lang="en">
<head>
<meta charset="utf-8">
<title>Calder Grove Investment Company</title>
<link href="https://fonts.googleapis.com/css2?family=EB+Garamond:wght@400;500;600&display=swap" rel="stylesheet">
<style>
  :root {
    --navy: #0b0b70;
    --gold: #8f6a0c;
    --white: #ffffff;
    --rule: #c9c9c9;
    --panel-top: #5d5f5f;
    --panel-bottom: #383a3c;
    --wing: #d2d2d2;
    --footer-text: #444444;
  }
  * { margin: 0; padding: 0; box-sizing: border-box; }
  html, body { width: 1200px; height: 762px; overflow: hidden; background: var(--white); }
  body { font-family: "EB Garamond", "Palatino Linotype", serif; position: relative; }

  .site-header { position: absolute; top: 0; left: 0; width: 1200px; height: 117px; text-align: center; }
  .brand-name { position: absolute; top: 8px; width: 100%; font-size: 58px; font-weight: 500; color: var(--navy); letter-spacing: 0.2px; }
  .brand-tag { position: absolute; top: 70px; width: 100%; font-size: 24px; color: var(--gold); }

  .hero { position: absolute; top: 117px; left: 0; width: 1200px; height: 433px; border-top: 3px solid var(--rule); border-bottom: 2px solid var(--rule); overflow: hidden; }
  .hero-photo { position: absolute; inset: 0;
    background: linear-gradient(180deg, #4f6f99 0%, #7c8fa8 22%, #c9cdd2 45%, #a9aaa7 65%, #5c5f55 100%); }
  .hero-photo::after { content: ""; position: absolute; left: 0; right: 0; bottom: 0; height: 46px; background: rgba(30,30,30,0.55); }

  .main-nav { position: absolute; top: 20px; left: 131px; width: 938px; height: 48px; background: var(--navy); border-radius: 16px; border: 2px solid #e6e6e6; display: flex; align-items: center; overflow: hidden; }
  .main-nav a { color: var(--white); text-decoration: none; font-size: 21px; height: 100%; display: flex; align-items: center; justify-content: center; position: relative; }
  .main-nav a + a::before { content: ""; position: absolute; left: 0; top: 15px; height: 18px; border-left: 1px solid #4d8bc0; }
  .main-nav a.active { background: var(--gold); font-weight: 600; }
  .main-nav a.active::before, .main-nav a.active + a::before { display: none; }

  .hero-copy { position: absolute; left: 133px; top: 246px; color: var(--white); font-size: 32px; line-height: 43px; }

  .welcome-wings { position: absolute; left: 112px; top: 548px; }
  .welcome { position: absolute; left: 131px; top: 517px; width: 938px; height: 140px; border-radius: 18px 18px 0 0; background: linear-gradient(180deg, var(--panel-top), var(--panel-bottom)); color: var(--white); }
  .welcome-title { position: absolute; left: 17px; top: 32px; font-size: 31px; font-weight: 500; }
  .welcome-brand { position: absolute; left: 17px; top: 70px; font-size: 20.5px; }
  .welcome-brand small { display: block; font-size: 9.5px; text-align: center; margin-top: -2px; }
  .welcome-divider { position: absolute; left: 297px; top: 24px; height: 100px; border-left: 1px solid #777; }
  .welcome-text { position: absolute; left: 313px; top: 18px; width: 610px; font-size: 18px; line-height: 25.5px; }

  .site-footer { position: absolute; left: 131px; top: 703px; width: 938px; border-top: 1px solid #d8d8d8; color: var(--footer-text); }
  .copyright { position: absolute; left: 2px; top: 8px; font-size: 15.5px; white-space: nowrap; }
  .contact { position: absolute; right: 2px; top: 6px; display: flex; align-items: center; gap: 10px; font-size: 20px; white-space: nowrap; }
  .contact svg { display: block; }
  .bottom-rule { position: absolute; left: 0; top: 760px; width: 1200px; height: 2px; background: var(--gold); }
</style>
</head>
<body>
  <header class="site-header">
    <div class="brand-name">Calder Grove Investment Company</div>
    <div class="brand-tag">Separately Managed Accounts</div>
  </header>

  <section class="hero">
    <div class="hero-photo" role="img" aria-label="Photograph of a white clapboard railway station building under a blue sky"></div>
    <nav class="main-nav">
      <a class="active" href="#" style="width:95px">Home</a>
      <a href="#" style="width:145px">Philosophy</a>
      <a href="#" style="width:160px">Performance</a>
      <a href="#" style="width:100px">Team</a>
      <a href="#" style="width:113px">Letters</a>
      <a href="#" style="width:170px">Commentary</a>
      <a href="#" style="width:151px">Contact Us</a>
    </nav>
    <p class="hero-copy">We Manage Assets For Both<br>Individuals And Institutions In Dallas, TX</p>
  </section>

  <svg class="welcome-wings" width="976" height="110" viewBox="0 0 976 110" aria-hidden="true">
    <polygon points="0,0 19,0 19,108" fill="var(--wing)"/>
    <polygon points="957,0 976,0 957,108" fill="var(--wing)"/>
  </svg>

  <section class="welcome">
    <h1 class="welcome-title">Welcome To</h1>
    <div class="welcome-brand">Calder Grove Investment Co.<small>Separately Managed Accounts</small></div>
    <div class="welcome-divider"></div>
    <p class="welcome-text">We founded Calder Grove Investment Company in 1999, initially managing wealth from our family and friends in the town of Calder Grove. The high expectations of our original investors is a key contributor to our value driven investment philosophy.</p>
  </section>

  <footer class="site-footer">
    <div class="copyright">Copyright © 2017&nbsp; Calder Grove Investment Company. All Right Reserved</div>
    <div class="contact">
      <svg width="18" height="14" viewBox="0 0 18 14" aria-hidden="true"><rect width="18" height="14" rx="1" fill="#444"/><polyline points="1,1 9,8 17,1" fill="none" stroke="#fff" stroke-width="1.6"/></svg>
      <span style="margin-left:6px">info@caldergrove.example</span>
      <svg width="26" height="26" viewBox="0 0 26 26" aria-hidden="true" style="margin-left:4px"><circle cx="13" cy="13" r="11.5" fill="none" stroke="#444" stroke-width="1.4"/><path d="M10 7c-1 1-2 3 0 7s4 6 6 6l1.5-1.5-2-2.5-1.5 1c-1-.5-2.5-2.5-3-4l1.3-1L11 7z" fill="#444"/></svg>
      <span style="margin-left:4px">555-014-3456</span>
    </div>
  </footer>
  <div class="bottom-rule"></div>
</body>
</html>
```